Dorrow Hollow Ranch all natural beef packaging

I would like a custom label to affix to my packages of steaks, roasts, and burgers. The packaging label should be simple and represent the all natural, healthy and humane way we raise our grass finished and natural grain finished beef. check out www.dorrowhollowranch.example for photos of the ranch and information about our cattle.

Target Market(s)

consumers who wish to purchase beef that is born and raised in Ohio, never given any antibiotics, implants, or hormones. Cattle are never confined, always on pasture, even when finished on grain. Humane treatment of the animals which are handled by horseback and on foot.

Industry/Entity Type

Ranch

Requirements
Must have
• Must be able to incorporate the Prairie Forage Alliance label.
• http://www.prairieforagealliance.example/
• I like dark colors, rich and earthy, but maybe on a white background to stand out on the clear plastic wrap over the beef. Imagine you're buying a steak at Halvins and look at how the packaging stands off from the color of the meat.
Nice to have
• I would like a very simple label that incorporates some icon or picture of a calf or cow. See my website www.dorrowhollowranch.example

```html
<!DOCTYPE html>
<html lang="en">
<head>
<meta charset="utf-8">
<title>Dorrow Hollow Ranch – Beef Package Label</title>
<link href="https://fonts.googleapis.com/css2?family=Rye&family=Oswald:wght@500;700&display=swap" rel="stylesheet">
<style>
  :root {
    --backdrop: #e4e4e6;
    --label-cream: #f9ebcb;
    --label-cream-deep: #f1dcae;
    --ink: #141210;
    --banner-text: #f7d417;
    --badge-green: #1f7a4a;
    --badge-yellow: #f5d40f;
    --claim-green: #2f8a3e;
    --photo-dark: #2a2826;
    --photo-mid: #5b5752;
  }
  * { margin: 0; padding: 0; box-sizing: border-box; }
  html, body { width: 863px; height: 1200px; overflow: hidden; }
  body {
    background: radial-gradient(ellipse at center, #f7f7f8 0%, var(--backdrop) 75%);
    position: relative;
  }
  .package-label {
    position: absolute;
    left: 41px;
    top: 377px;
    width: 780px;
    height: 446px;
    overflow: visible;
    filter: drop-shadow(0 10px 14px rgba(0,0,0,0.35));
  }
  .ranch-name {
    font-family: "Rye", serif;
    font-size: 36px;
    fill: var(--ink);
    letter-spacing: 1px;
  }
  .product-banner-text {
    font-family: "Oswald", sans-serif;
    font-weight: 700;
    font-size: 34px;
    fill: var(--banner-text);
  }
  .claim {
    font-family: "Oswald", sans-serif;
    font-weight: 500;
    font-size: 15px;
    fill: var(--claim-green);
  }
  .tick { fill: none; stroke: var(--claim-green); stroke-width: 3; stroke-linecap: round; stroke-linejoin: round; }
</style>
</head>
<body>
  <svg class="package-label" viewBox="0 0 780 446" xmlns="http://www.w3.org/2000/svg" aria-label="Dorrow Hollow Ranch 100% grassfed beef label">
    <defs>
      <radialGradient id="label-paper" cx="50%" cy="45%" r="60%">
        <stop offset="0%" stop-color="var(--label-cream)"/>
        <stop offset="100%" stop-color="var(--label-cream-deep)"/>
      </radialGradient>
      <linearGradient id="calf-tone" x1="0" y1="0" x2="0" y2="1">
        <stop offset="0%" stop-color="var(--photo-mid)"/>
        <stop offset="100%" stop-color="var(--photo-dark)"/>
      </linearGradient>
      <path id="name-arc" d="M 140 125 Q 400 -5 700 125"/>
    </defs>

    <!-- label body -->
    <ellipse class="label-oval" cx="390" cy="223" rx="384" ry="217" fill="url(#label-paper)" stroke="var(--ink)" stroke-width="9"/>

    <!-- ranch name -->
    <text class="ranch-name" text-anchor="middle">
      <textPath href="#name-arc" startOffset="50%">DORROW HOLLOW RANCH</textPath>
    </text>

    <!-- calf photograph area -->
    <rect class="calf-photo" x="320" y="95" width="220" height="112" rx="10" fill="url(#calf-tone)" role="img" aria-label="Photograph of a young black calf standing in pasture"/>

    <!-- product banner -->
    <rect class="product-banner" x="217" y="205" width="386" height="49" fill="var(--ink)"/>
    <text class="product-banner-text" x="410" y="243" text-anchor="middle">100% GRASSFED BEEF</text>

    <!-- certification badges -->
    <circle class="alliance-badge" cx="132" cy="168" r="36" fill="var(--badge-green)" stroke="#ffffff" stroke-width="3" role="img" aria-label="Prairie Forage Alliance certification badge"/>
    <rect class="inspection-badge" x="90" y="214" width="82" height="104" fill="var(--badge-yellow)" role="img" aria-label="State inspection and approval badge"/>

    <!-- product claims -->
    <g class="claims">
      <polyline class="tick" points="610,157 615,163 624,152"/>
      <text class="claim" x="628" y="164">NO ANTIBIOTICS.</text>
      <polyline class="tick" points="594,177 599,183 608,172"/>
      <text class="claim" x="612" y="184">NO ADDED HORMONES.</text>
      <polyline class="tick" points="640,197 645,203 654,192"/>
      <text class="claim" x="658" y="204">NO GRAINS.</text>
    </g>
  </svg>
</body>
</html>
```